Meridale Bed Company Needs Business Card

Looking for a very nice looking business card. Creative but not extravagant. We sell beds and pillows across the U.S. and need something professional but catchy. I have attached the logo.

Name : Devin Holt
Title : President
Phone : (800) 471-2960
Email: sleep@quilmora.com
Website: www.quilmora.com

Can be single-sided or double-sided
horizontal or vertical

Can use Blues/Greys

Target Market(s)

Mass Market

Industry/Entity Type

Retail

Contact Information for Business Card

Name : Devin Holt
Title : President
Phone : (800) 471-2960
Email: sleep@quilmora.com
Website: www.quilmora.com

Requirements
Must have
• Clean, Modern, Smooth
• Can use Blues/Greys
• On the other side without the information - have something simple like www.quilmora.com or our logo
Nice to have
• Surprise me
Should not have
• Nothing crazy, nothing cluttered

```html
<!DOCTYPE html>
<html lang="en">
<head>
<meta charset="utf-8">
<title>Quilmora Business Card</title>
<link rel="stylesheet" href="https://fonts.googleapis.com/css2?family=Montserrat:wght@300;400;500&display=swap">
<style>
  :root {
    --backdrop: #2f2f30;
    --card-blue: #1e93c7;
    --card-blue-deep: #1a86b9;
    --card-white: #f4f4f4;
    --brand-blue: #1b8dc4;
    --ink-grey: #555a5e;
    --url-light: #d6eef8;
  }
  * { margin: 0; padding: 0; box-sizing: border-box; }
  html, body {
    width: 1200px;
    height: 787px;
    overflow: hidden;
    background: var(--backdrop);
    font-family: "Montserrat", Arial, sans-serif;
  }
  .stage {
    position: relative;
    width: 1200px;
    height: 787px;
  }
  .card {
    position: absolute;
    top: 239px;
    width: 535px;
    height: 299px;
    border-radius: 18px;
    overflow: hidden;
  }
  .card-back {
    left: 47px;
    background: linear-gradient(135deg, var(--card-blue-deep), var(--card-blue));
  }
  .back-url {
    position: absolute;
    left: 344px;
    top: 279px;
    top: 42px;
    font-size: 13px;
    font-weight: 500;
    letter-spacing: 1.2px;
    color: var(--url-light);
  }
  .card-front {
    left: 629px;
    background: var(--card-white);
  }
  .brand-name {
    position: absolute;
    left: 0;
    right: 0;
    top: 66px;
    text-align: center;
    padding-left: 130px;
    font-size: 56px;
    font-weight: 300;
    letter-spacing: 1px;
    color: var(--brand-blue);
  }
  .person {
    position: absolute;
    left: 42px;
    top: 188px;
  }
  .person-name {
    font-size: 21px;
    font-weight: 500;
    color: var(--ink-grey);
    line-height: 1.2;
  }
  .person-title {
    margin-top: 4px;
    font-size: 14px;
    font-weight: 400;
    color: var(--brand-blue);
    letter-spacing: 0.3px;
  }
  .contact {
    position: absolute;
    left: 348px;
    top: 188px;
  }
  .contact-icons {
    display: flex;
    gap: 6px;
    margin-bottom: 5px;
  }
  .contact-icons svg { width: 18px; height: 18px; display: block; }
  .contact-line {
    font-size: 14.5px;
    font-weight: 400;
    line-height: 17px;
    color: var(--ink-grey);
    letter-spacing: 0.3px;
  }
  .contact-line.web { color: var(--brand-blue); }
</style>
</head>
<body>
<main class="stage">
  <section class="card card-back" aria-label="Card back">
    <p class="back-url">www.quilmora.com</p>
  </section>

  <section class="card card-front" aria-label="Card front">
    <h1 class="brand-name">quilmora</h1>

    <div class="person">
      <p class="person-name">Devin Holt</p>
      <p class="person-title">President</p>
    </div>

    <div class="contact">
      <div class="contact-icons">
        <svg viewBox="0 0 20 20" aria-label="Phone">
          <circle cx="10" cy="10" r="10" fill="var(--brand-blue)"/>
          <path d="M5 8.5c0-1.5 2.2-2.5 5-2.5s5 1 5 2.5l-1.8.6-.6-1.4h-5.2l-.6 1.4z" fill="#fff"/>
          <rect x="6.5" y="9.5" width="7" height="4.5" rx="1" fill="#fff"/>
          <circle cx="10" cy="11.7" r="1.2" fill="var(--brand-blue)"/>
        </svg>
        <svg viewBox="0 0 20 20" aria-label="Email">
          <circle cx="10" cy="10" r="10" fill="var(--brand-blue)"/>
          <rect x="5" y="6.5" width="10" height="7" rx="0.8" fill="none" stroke="#fff" stroke-width="1.3"/>
          <path d="M5.3 7l4.7 3.8L14.7 7" fill="none" stroke="#fff" stroke-width="1.3"/>
        </svg>
        <svg viewBox="0 0 20 20" aria-label="Website">
          <circle cx="10" cy="10" r="10" fill="var(--brand-blue)"/>
          <g fill="none" stroke="#fff" stroke-width="1.1">
            <circle cx="10" cy="10" r="5"/>
            <ellipse cx="10" cy="10" rx="2.2" ry="5"/>
            <path d="M5 10h10M6 7.5h8M6 12.5h8"/>
          </g>
        </svg>
      </div>
      <p class="contact-line">(800) 471-2960</p>
      <p class="contact-line">sleep@quilmora.com</p>
      <p class="contact-line web">www.quilmora.com</p>
    </div>
  </section>
</main>
</body>
</html>
```